Gift Cards in the Mail Envelope

Mailing out gift cards in the envelope. Need an eye popping envelope. Please look at the enclosed images. The envelope should look like that.

Low design quality

```html
<!DOCTYPE html>
<html lang="en">
<head>
<meta charset="UTF-8">
<title>Gift Card Mailing Envelope</title>
<link href="https://fonts.googleapis.com/css2?family=Lato:wght@400&display=swap" rel="stylesheet">
<style>
  :root {
    --teal: #03796f;
    --logo-grey: #9a9d9f;
    --paper: #ffffff;
    --ink: #2a2a2a;
    --backdrop: #e4e5e6;
  }
  html, body {
    margin: 0;
    padding: 0;
    width: 1200px;
    height: 1200px;
    overflow: hidden;
    background: var(--backdrop);
  }
  .canvas {
    position: relative;
    width: 1200px;
    height: 1200px;
  }
  .envelope {
    position: absolute;
    background: var(--paper);
    box-shadow: 0 2px 6px rgba(0, 0, 0, 0.25);
    overflow: hidden;
  }
  .envelope-front {
    left: 190px;
    top: 192px;
    width: 818px;
    height: 409px;
  }
  .brand-band {
    position: absolute;
    top: 83px;
    height: 45px;
    background: var(--teal);
  }
  .brand-band-left {
    left: 0;
    width: 62px;
  }
  .brand-band-right {
    left: 246px;
    right: 0;
  }
  .logo-block {
    position: absolute;
    left: 76px;
    top: 30px;
    width: 152px;
    height: 151px;
    background: var(--logo-grey);
  }
  .return-address {
    position: absolute;
    left: 38px;
    top: 204px;
    width: 240px;
    margin: 0;
    text-align: center;
    font-family: "Lato", sans-serif;
    font-size: 15.5px;
    line-height: 19px;
    color: var(--ink);
  }
  .envelope-back {
    left: 192px;
    top: 703px;
    width: 814px;
    height: 404px;
  }
  .envelope-back svg {
    display: block;
  }
  .flap {
    fill: var(--teal);
  }
</style>
</head>
<body>
  <main class="canvas">
    <section class="envelope envelope-front" aria-label="Envelope front">
      <div class="brand-band brand-band-left"></div>
      <div class="brand-band brand-band-right"></div>
      <div class="logo-block"></div>
      <p class="return-address">421, Address line goes here<br>Country Name, 45452</p>
    </section>

    <section class="envelope envelope-back" aria-label="Envelope back">
      <svg width="814" height="404" viewBox="0 0 814 404" xmlns="http://www.w3.org/2000/svg">
        <path class="flap" d="M6,0 L808,0 L808,30 Q808,48 792,55 L420,205 Q408,210 396,205 L22,55 Q6,48 6,30 Z"/>
      </svg>
    </section>
  </main>
</body>
</html>
```